Economics of an Assumption vs Obtaining a New Loan at Current Market Rate

I need to marketing flyer that has fields that calculate mortgage payments amongst other calculations. I have a rough draft that I will attach.

The idea is to provide a tool for a real estate agent to use to illustrate to a potential buyer what a payment would be if they assumed the existing loan on the house or took out a new loan at current market.

The flyer needs to be able to allow an agent to drop in their logo, photo, and contact along with the loan officers photo and contact info.

You can google open house flyer to see examples of what the overall artwork and presentation can look like.

Target Market(s)

Home Buyers

Industry/Entity Type

Real Estate

Colors
F0912C
F2A743
F7CA91
FBE8D2
FDF5EE
EE7325
F08F49
F5BC92
FAE3D3
FDF4ED

Requirements
Must have
• A way to calculate mortgage payment
Nice to have
• Photo and logo drop ins

```html
<!DOCTYPE html>
<html lang="en">
<head>
<meta charset="utf-8">
<title>House For Sale – Mortgage Comparison Flyer</title>
<link href="https://fonts.googleapis.com/css2?family=Poppins:wght@400;500;600;800&family=Oswald:wght@600&display=swap" rel="stylesheet">
<style>
  :root {
    --orange: #EE7325;
    --orange-dark: #8a3d10;
    --ink: #2a2a2a;
    --panel: #2e2e2e;
    --paper: #ffffff;
    --field-line: #555555;
    --footer-gray: #d6d6d6;
  }
  * { box-sizing: border-box; margin: 0; padding: 0; }
  html, body { width: 691px; height: 1200px; overflow: hidden; background: var(--paper); }
  body { font-family: "Poppins", sans-serif; color: var(--ink); }
  .flyer { position: relative; width: 691px; height: 1200px; background: var(--paper); overflow: hidden; }

  /* Header */
  .brand { position: absolute; left: 70px; top: 70px; display: flex; align-items: center; gap: 12px; }
  .brand-mark { width: 34px; height: 34px; background: var(--orange); }
  .brand-name { font-size: 46px; font-weight: 500; color: var(--orange); letter-spacing: 0.5px; }
  .headline { position: absolute; left: 343px; top: 48px; }
  .headline-top { font-size: 56px; font-weight: 800; line-height: 1; color: var(--ink); letter-spacing: 0.5px; }
  .headline-bottom { margin-top: 8px; display: inline-block; background: var(--orange); color: #fff; font-size: 54px; font-weight: 800; line-height: 1; padding: 8px 12px 6px; }

  /* Photo + price band */
  .hero-photo { position: absolute; left: 0; top: 212px; width: 691px; height: 250px;
    background: linear-gradient(180deg, #c9b7a7 0%, #8e7f74 35%, #5a5148 60%, #3b3a36 80%, #4b5340 100%); }
  .price-band { position: absolute; left: 0; top: 462px; width: 691px; height: 52px; background: var(--panel);
    display: flex; align-items: center; justify-content: center; gap: 14px; }
  .price-label { color: #fff; font-size: 26px; font-weight: 600; letter-spacing: 0.5px; }
  .price-field { width: 160px; height: 24px; background: #fff; }

  /* Mortgage panels */
  .mortgage { position: absolute; top: 532px; width: 298px; height: 292px; }
  .mortgage.current { left: 36px; }
  .mortgage.new { left: 358px; }
  .mortgage-tab { position: absolute; left: 0; top: 0; width: 298px; height: 38px; }
  .mortgage-title { position: absolute; left: 0; top: 0; width: 298px; height: 34px; display: flex; align-items: center; justify-content: center;
    font-family: "Oswald", sans-serif; font-weight: 600; color: #fff; font-size: 17px; letter-spacing: 0.2px; }
  .mortgage-body { position: absolute; left: 0; top: 34px; width: 298px; height: 258px; background: var(--panel); padding: 26px 14px 0; }
  .row { display: flex; align-items: center; justify-content: space-between; height: 22px; margin-bottom: 16px; }
  .row-label { color: #fff; font-size: 13px; line-height: 1.15; }
  .input { background: #fff; height: 22px; width: 124px; font-size: 12px; color: var(--ink); padding: 3px 12px; line-height: 16px; white-space: nowrap; }
  .input.wide { width: 160px; padding: 3px 8px; }
  .row.tall { height: 38px; }
  .input.tall { height: 38px; width: 176px; line-height: 14px; padding-top: 4px; }
  .total { display: flex; height: 30px; margin-top: 19px; border: 1px solid #fff; }
  .total-label { width: 144px; color: var(--orange); font-size: 18px; padding-left: 10px; line-height: 28px; }
  .total-value { flex: 1; background: #fff; }

  /* Calculator fields */
  .field-line { position: absolute; display: flex; align-items: center; gap: 10px; font-size: 13px; color: var(--ink); }
  .box { border: 1px solid var(--field-line); height: 26px; font-size: 12px; padding: 0 8px; line-height: 24px; color: var(--ink); white-space: nowrap; }
  .note { font-size: 9px; line-height: 1; border-bottom: 1px solid var(--field-line); padding-bottom: 2px; }

  /* Ribbon */
  .ribbon { position: absolute; left: 128px; top: 996px; width: 436px; height: 30px; }
  .ribbon-text { position: absolute; left: 0; top: 0; width: 436px; height: 30px; display: flex; align-items: center; justify-content: center;
    color: #fff; font-weight: 600; font-size: 15px; }

  /* Drop zones */
  .footer-band { position: absolute; left: 0; top: 1148px; width: 691px; height: 52px; background: var(--footer-gray); }
  .drop { position: absolute; top: 1050px; display: flex; gap: 8px; }
  .drop-label { font-size: 13px; line-height: 1.25; text-align: right; text-transform: uppercase; }
  .drop-box { width: 72px; height: 112px; border: 1px solid var(--field-line); background: #fff; }
</style>
</head>
<body>
<main class="flyer">

  <header>
    <div class="brand">
      <span class="brand-mark"></span>
      <span class="brand-name">Nestora</span>
    </div>
    <div class="headline">
      <div class="headline-top">HOUSE</div>
      <div class="headline-bottom">FOR SALE</div>
    </div>
  </header>

  <div class="hero-photo" role="img" aria-label="Photo of a modern two-storey house at dusk with stone facade and wooden garage door"></div>
  <div class="price-band">
    <span class="price-label">PURCHASE PRICE :</span>
    <span class="price-field"></span>
  </div>

  <section class="mortgage current">
    <svg class="mortgage-tab" viewBox="0 0 298 38" aria-hidden="true">
      <polygon points="0,38 10,28 10,38" fill="#8a3d10"/>
      <polygon points="298,38 288,28 288,38" fill="#8a3d10"/>
      <polygon points="14,0 284,0 298,34 0,34" fill="#EE7325"/>
    </svg>
    <div class="mortgage-title">CURRENT MORTGAGE</div>
    <div class="mortgage-body">
      <div class="row"><span class="row-label">Loan amount:</span><span class="input">Allow input</span></div>
      <div class="row"><span class="row-label">Interest rate :</span><span class="input">Allow input</span></div>
      <div class="row"><span class="row-label">Principal &amp; Interest:</span><span class="input">Allow input</span></div>
      <div class="row"><span class="row-label">Mortgage Insurance:</span><span class="input">Allow input</span></div>
      <div class="total"><span class="total-label">TOTAL</span><span class="total-value"></span></div>
    </div>
  </section>

  <section class="mortgage new">
    <svg class="mortgage-tab" viewBox="0 0 298 38" aria-hidden="true">
      <polygon points="0,38 10,28 10,38" fill="#8a3d10"/>
      <polygon points="298,38 288,28 288,38" fill="#8a3d10"/>
      <polygon points="14,0 284,0 298,34 0,34" fill="#EE7325"/>
    </svg>
    <div class="mortgage-title">NEW MORTGAGE 10%. DOWN PAYMENT</div>
    <div class="mortgage-body">
      <div class="row"><span class="row-label">Loan amount:</span><span class="input wide">10% of purchase price</span></div>
      <div class="row"><span class="row-label">Market rate:</span><span class="input">Input</span></div>
      <div class="row"><span class="row-label">Principal Interest:</span><span class="input">Input%</span></div>
      <div class="row tall"><span class="row-label">Mortgage<br>insurace:</span><span class="input tall">Principal Interest+<br>Montgage &amp; +insusance</span></div>
      <div class="total"><span class="total-label">TOTAL</span><span class="total-value"></span></div>
    </div>
  </section>

  <div class="field-line" style="left:36px; top:850px;">
    <span>Years</span><span class="box" style="width:58px">Input</span>
    <span style="margin-left:12px">Months</span><span class="box" style="width:58px">Input</span>
    <span class="note">LEFT ON<br>LOAN</span>
  </div>
  <div class="field-line" style="left:36px; top:898px;">
    <span>Telta</span><span class="box" style="width:246px">Purchase price minus loan amount</span>
  </div>
  <div class="field-line" style="left:358px; top:850px;">
    <span>Term</span><span class="box" style="width:206px">Input</span><span>years</span>
  </div>
  <div class="field-line" style="left:358px; top:898px;">
    <span>DOWN Payment Amount</span><span class="box" style="width:122px"></span>
  </div>
  <div class="field-line" style="left:152px; top:946px;">
    <span>Payment difference</span><span class="box" style="width:254px">Difference Between Totals</span>
  </div>

  <div class="ribbon">
    <svg width="436" height="30" viewBox="0 0 436 30" aria-hidden="true">
      <polygon points="0,0 436,0 422,15 436,30 0,30 14,15" fill="#EE7325"/>
    </svg>
    <div class="ribbon-text">THIS PROPERTY IS AN "ASSUMABLE LOW RATE HOME"</div>
  </div>

  <div class="footer-band"></div>
  <div class="drop" style="left:36px;"><span class="drop-label">Drop<br>Photo</span><span class="drop-box"></span></div>
  <div class="drop" style="left:196px;"><span class="drop-label">Drop<br>Contact<br>Info</span><span class="drop-box"></span></div>
  <div class="drop" style="left:376px;"><span class="drop-label">Drop<br>Photo</span><span class="drop-box"></span></div>
  <div class="drop" style="left:536px;"><span class="drop-label">Drop<br>Logo</span><span class="drop-box"></span></div>

</main>
</body>
</html>
```